lantern pathway for children needs a website designer

We need a website designer for our new extension to our company known as 'lantern pathway' providing shadow support services to children based in Singapore. We are a sister branch of a private clinic 'Bright horizons' providing speech language, occupational, and educational therapy to children.

We would like to use our own photos. So the selected design should have a frame with pictures to give us an idea but we will replace them with our own. We will be needing help with inputting information and changing information throughout.

We would like to see designs that are simple, and professional. We have a logo (see attached). The result should convey professionalism in shadow support, fostering independent thinking and moving students towards self-learning.

Target Market(s)

Teachers, psychologists, parents

Industry/Entity Type

Clinic

Requirements
Should not have
• too distracting colours

```html
<!DOCTYPE html>
<html lang="en">
<head>
<meta charset="utf-8">
<title>Lantern Pathway – Shadow Support</title>
<link rel="stylesheet" href="https://fonts.googleapis.com/css2?family=Source+Sans+3:wght@400;600;700&family=Roboto+Condensed:wght@700&family=Arimo:wght@400&display=swap">
<style>
:root{
  --brand-red:#8b0000;
  --ink:#222;
  --text:#333;
  --grey-bar:#5a5a5a;
  --footer:#353535;
  --rule:#dddddd;
  --white:#fff;
}
*{box-sizing:border-box;margin:0;padding:0}
html,body{width:1125px;height:1200px;overflow:hidden;background:var(--white)}
body{position:relative;font-family:"Source Sans 3",sans-serif;color:var(--text)}
.abs{position:absolute}

/* header */
.top-line{left:0;top:0;width:1125px;height:4px;background:var(--brand-red)}
.site-header{left:0;top:4px;width:1125px;height:120px;background:linear-gradient(#fff,#f1f1f1)}
.brand{left:133px;top:40px;display:flex;align-items:center;gap:8px}
.brand-mark{width:18px;height:18px;background:var(--brand-red)}
.brand-name{font-weight:700;font-size:30px;color:var(--brand-red);line-height:1}
.contact{right:133px;top:20px;text-align:right;font-size:12px;color:var(--brand-red);line-height:24px}
.contact b{font-weight:700}
.main-nav{right:133px;top:73px;display:flex;height:29px;align-items:center}
.main-nav a{font-size:12.3px;font-weight:600;color:var(--ink);text-decoration:none;padding:0 11.5px;line-height:29px}
.main-nav a:last-child{padding-right:0}
.main-nav a.active{background:var(--brand-red);color:var(--white);padding:0 11px}

/* hero */
.hero{left:0;top:124px;width:1125px;height:449px;background:linear-gradient(100deg,#c9a07a 0%,#8fa8b4 35%,#c9b08c 55%,#a84a3c 80%,#8a2e2a 100%)}
.slider-dots{left:537px;top:457px;display:flex;gap:6px}
.slider-dots span{width:12px;height:12px;border-radius:50%;background:#d8d8d8;border:2px solid #fff}
.slider-dots span.on{background:var(--brand-red)}
.feature-band{left:0;top:484px;width:1125px;height:89px;background:rgba(60,60,60,.45)}
.feature-tab{top:501px;width:193px;height:55px;background:var(--white);display:flex;align-items:center;gap:8px;padding-left:10px;font-weight:600;font-size:11px;color:#222;white-space:nowrap}
.feature-tab.primary{color:var(--brand-red);font-size:13.5px;padding-left:28px;gap:20px}
.feature-tab svg{flex:none}
.band-arrow{top:521px;width:15px;height:15px;border-radius:50%;background:#b00000}

/* about */
.section-title{font-family:"Roboto Condensed",sans-serif;font-weight:700;font-size:15.5px;color:var(--brand-red);text-transform:uppercase}
.about-rule{left:133px;top:620px;width:673px;height:1px;background:var(--rule)}
.about-photo{left:133px;top:629px;width:263px;height:149px;border:4px solid #fff;box-shadow:0 0 3px rgba(0,0,0,.25);background:linear-gradient(120deg,#e6ddd0,#c9b49a 50%,#7d8a99)}
.about-text{left:406px;top:628px;width:396px;font-family:Arimo,sans-serif;font-size:12.6px;line-height:15.8px;color:#222;text-align:justify}
.about-text p+p{margin-top:15.8px;text-align:left}
.side-list{list-style:none;font-size:11.6px;color:#222}
.side-list li{position:relative;padding-left:12px;height:21.5px}
.side-list li::before{content:"";position:absolute;left:0;top:4px;border-left:6px solid var(--brand-red);border-top:4px solid transparent;border-bottom:4px solid transparent}
.divider{left:133px;top:808px;width:860px;height:8px;background:radial-gradient(ellipse at 50% 0,rgba(0,0,0,.14),transparent 70%)}

/* services */
.service-card{top:875px;width:263px;height:206px}
.service-photo{width:263px;height:169px}
.service-bar{width:263px;height:37px;background:var(--grey-bar);display:flex;align-items:center;color:#fff;font-weight:700;font-size:15.5px;text-transform:uppercase}
.service-bar.active{background:var(--brand-red)}
.service-bar .chev{width:26px;height:26px;border-radius:0 13px 13px 0;display:flex;align-items:center;justify-content:center;margin-right:12px;background:var(--brand-red)}
.service-bar.active .chev{background:#555}

/* footer */
.site-footer{left:0;top:1110px;width:1125px;height:90px;background:var(--footer)}
.footer-nav{left:134px;top:1133px;font-size:11px;color:#fff}
.footer-nav span{margin:0 4px}
.copyright{left:134px;top:1162px;font-family:Arimo,sans-serif;font-size:10.5px;color:#eee}
.social{left:858px;top:1140px;display:flex;gap:7px}
.social span{width:28px;height:28px;border-radius:50%}
</style>
</head>
<body>
<div class="abs top-line"></div>
<header class="abs site-header"></header>
<div class="abs brand"><span class="brand-mark"></span><span class="brand-name">Lantern Pathway</span></div>
<div class="abs contact"><div><b>PHONE :</b> +65 6100 4820</div><div>enquiries@clearbrooktherapy.sg</div></div>
<nav class="abs main-nav">
  <a class="active" href="#">HOME</a><a href="#">ABOUT US</a><a href="#">OUR SERVICES</a><a href="#">SHADOW SUPPORT</a><a href="#">FOR SUPPORT</a><a href="#">CONTACT US</a>
</nav>

<section class="abs hero" role="img" aria-label="Photo of a smiling young girl with a teacher in a bright classroom"></section>
<div class="abs slider-dots"><span class="on"></span><span></span><span></span></div>
<div class="abs feature-band"></div>
<div class="abs band-arrow" style="left:144px"></div>
<div class="abs band-arrow" style="left:969px"></div>
<div class="abs feature-tab primary" style="left:163px">
  <svg width="20" height="20" viewBox="0 0 20 20" fill="none" stroke="#222" stroke-width="2.4"><path d="M4 9a6 6 0 0 1 10-3l2 2M16 11a6 6 0 0 1-10 3l-2-2"/><path d="M16 3v5h-5M4 17v-5h5" stroke-width="2"/></svg>SHADOW SUPPORT</div>
<div class="abs feature-tab" style="left:365px">
  <svg width="22" height="22" viewBox="0 0 22 22" fill="none" stroke="#111" stroke-width="2.4"><path d="M6.5 5.5a8 8 0 1 0 9 0"/><path d="M11 2v9"/></svg>WHAT ARE ITS ADVANTAGES?</div>
<div class="abs feature-tab" style="left:567px">
  <svg width="22" height="22" viewBox="0 0 22 22" fill="none" stroke="#111" stroke-width="2.2"><circle cx="11" cy="11" r="9.5"/><path d="M7.5 7.5l7 7M14.5 7.5l-7 7" stroke-width="2.8"/></svg>WHAT ARE ITS ADVANTAGES?</div>
<div class="abs feature-tab" style="left:769px">
  <svg width="18" height="18" viewBox="0 0 18 18" fill="none" stroke="#111" stroke-width="2.6"><path d="M2 2a14 14 0 0 1 14 14M2 8a8 8 0 0 1 8 8"/><circle cx="3.5" cy="14.5" r="2" fill="#111" stroke="none"/></svg>HOW DO I KNOW &nbsp; SHADOWING</div>

<h2 class="abs section-title" style="left:133px;top:590px">About Us</h2>
<div class="abs about-rule"></div>
<div class="abs about-photo" role="img" aria-label="Photo of a mother helping a young boy with his schoolwork"></div>
<div class="abs about-text">
  <p>Lantern Pathway is part of the Clearbrook Therapy Group of Companies, who are providing speech language therapy, occupational therapy and educational therapy services to both the Singapore and the Lantern Pathway aims to work in an integrated manner, respecting the work of the respective professionals involved and collaborating effectively.</p>
  <p>Lantern Pathway was borne out of our Speech language Pathologists’ frustration at a frequent lack of<br>carry-over of goals to a classroom setting by external shadows.</p>
</div>

<h2 class="abs section-title" style="left:833px;top:592px;font-size:13.5px">For Parents</h2>
<ul class="abs side-list" style="left:833px;top:619px">
  <li>Registration Form</li><li>Cost Estimation</li><li>For Schools</li>
</ul>
<h2 class="abs section-title" style="left:833px;top:697px;font-size:13.5px">School Terms</h2>
<ul class="abs side-list" style="left:833px;top:720px">
  <li>Achieve Your Goals</li><li>My Child Needs Support</li><li>Children who could benefit</li>
</ul>
<div class="abs divider"></div>

<h2 class="abs section-title" style="left:133px;top:836px">Our Services</h2>
<article class="abs service-card" style="left:133px">
  <div class="service-photo" role="img" aria-label="Photo of a doctor and a young woman during a therapy session" style="background:linear-gradient(110deg,#e9e4df,#9aa4b0 55%,#b34a3a)"></div>
  <div class="service-bar active"><span class="chev"><svg width="8" height="12" viewBox="0 0 8 12" fill="none" stroke="#fff" stroke-width="2"><path d="M1.5 1l5 5-5 5"/></svg></span>Train Shadows</div>
</article>
<article class="abs service-card" style="left:432px">
  <div class="service-photo" role="img" aria-label="Photo of a therapist playing with bubbles in front of a green chalkboard" style="background:linear-gradient(110deg,#d8d2cb,#3f7a64 50%,#2f5e4f)"></div>
  <div class="service-bar"><span class="chev"><svg width="8" height="12" viewBox="0 0 8 12" fill="none" stroke="#fff" stroke-width="2"><path d="M1.5 1l5 5-5 5"/></svg></span>Shadow Support</div>
</article>
<article class="abs service-card" style="left:729px">
  <div class="service-photo" role="img" aria-label="Photo of an educator working with a toddler in a playroom" style="background:linear-gradient(110deg,#c9b48c,#3a3440 45%,#c8407e 70%,#2d4fa0)"></div>
  <div class="service-bar"><span class="chev"><svg width="8" height="12" viewBox="0 0 8 12" fill="none" stroke="#fff" stroke-width="2"><path d="M1.5 1l5 5-5 5"/></svg></span>Educational Professionals</div>
</article>

<footer class="abs site-footer"></footer>
<div class="abs footer-nav">HOME<span>/</span>ABOUT US<span>/</span>OUR SERVICES<span>/</span>SHADOW SUPPORT<span>/</span>FOR SUPPORT<span>/</span>CONTACT US</div>
<div class="abs copyright">© 2014 Lantern Pathway. All Rights Reserved</div>
<div class="abs social" aria-label="Social links">
  <span style="background:#3b5a9a"></span><span style="background:#2aa3dc"></span><span style="background:#1f6fa8"></span><span style="background:#f07a1a"></span>
</div>
</body>
</html>
```